Business Card For Halvenmoor Financial Consulting

Hi, I would like a business card designed. Bold, modern.
Please use the same design as the logo. I have also attached the website design to see the overall theme.
Wordmark Font
Color: Hex: #01AEF7

```html
<!DOCTYPE html>
<html lang="en">
<head>
<meta charset="utf-8">
<title>Halvenmoor Financial Consulting – Business Card</title>
<link href="https://fonts.googleapis.com/css2?family=Montserrat:wght@400;500;700;800&display=swap" rel="stylesheet">
<style>
  :root {
    --card-navy: #15202b;
    --accent-blue: #01aef7;
    --text-white: #ffffff;
    --page-bg: #e6e8ea;
  }
  * { margin: 0; padding: 0; box-sizing: border-box; }
  html, body { width: 1200px; height: 798px; overflow: hidden; }
  body {
    background: var(--page-bg);
    font-family: "Montserrat", sans-serif;
    color: var(--text-white);
    position: relative;
  }
  .card {
    position: absolute;
    top: 244px;
    width: 540px;
    height: 310px;
    background: var(--card-navy);
    box-shadow: 0 10px 30px rgba(0,0,0,0.18);
  }
  .card--info { left: 40px; }
  .card--brand { left: 620px; }

  .brand {
    position: absolute;
    font-weight: 800;
    color: var(--text-white);
    letter-spacing: 0.04em;
    text-transform: uppercase;
    line-height: 1;
  }
  .card--info .brand { left: 38px; top: 112px; font-size: 22px; }
  .card--brand .brand {
    left: 50%;
    top: 50%;
    transform: translate(-50%, -50%);
    font-size: 40px;
  }

  .holder {
    position: absolute;
    right: 34px;
    top: 30px;
    text-align: right;
  }
  .holder__name {
    font-weight: 800;
    font-size: 22px;
    color: var(--accent-blue);
    text-transform: uppercase;
    letter-spacing: 0.01em;
  }
  .holder__title {
    font-weight: 500;
    font-size: 13px;
    margin-top: 2px;
  }

  .address {
    position: absolute;
    right: 34px;
    top: 150px;
    text-align: right;
    font-size: 13px;
    line-height: 1.45;
    font-weight: 500;
    font-style: normal;
  }

  .contacts {
    position: absolute;
    left: 38px;
    bottom: 26px;
    list-style: none;
  }
  .contacts li {
    display: flex;
    align-items: center;
    gap: 9px;
    font-size: 13px;
    font-weight: 500;
    height: 24px;
  }
  .contacts__icon {
    width: 18px;
    height: 18px;
    flex: none;
  }
</style>
</head>
<body>

  <section class="card card--info" aria-label="Business card, contact side">
    <div class="holder">
      <p class="holder__name">Dana Whitlock</p>
      <p class="holder__title">Senior Consultant</p>
    </div>

    <p class="brand">Halvenmoor</p>

    <address class="address">
      42-10 Larkspur Ave 14<br>
      Ridgeview, NY 11920
    </address>

    <ul class="contacts">
      <li>
        <svg class="contacts__icon" viewBox="0 0 18 18" aria-hidden="true">
          <circle cx="9" cy="9" r="9" fill="#01aef7"/>
          <path d="M6 5.2c.5-.4 1-.2 1.2.3l.6 1.3c.2.4 0 .8-.3 1l-.5.4c.4.9 1.1 1.6 2 2l.4-.5c.3-.3.7-.4 1-.2l1.3.6c.5.2.7.8.3 1.2-.8.9-1.900 1.1-3 .5-1.5-.8-2.7-2-3.500-3.500-.5-1-.4-2.200.5-3.100z" fill="#fff"/>
        </svg>
        +1 555 010 2468
      </li>
      <li>
        <svg class="contacts__icon" viewBox="0 0 18 18" aria-hidden="true">
          <circle cx="9" cy="9" r="9" fill="#01aef7"/>
          <rect x="4.5" y="6" width="9" height="6.5" fill="#fff"/>
          <path d="M4.5 6l4.5 3.6L13.5 6" fill="none" stroke="#01aef7" stroke-width="0.9"/>
        </svg>
        info@halvenmoor.com
      </li>
      <li>
        <svg class="contacts__icon" viewBox="0 0 18 18" aria-hidden="true">
          <circle cx="9" cy="9" r="9" fill="#01aef7"/>
          <circle cx="9" cy="9" r="4.6" fill="none" stroke="#fff" stroke-width="1.1"/>
          <ellipse cx="9" cy="9" rx="2" ry="4.6" fill="none" stroke="#fff" stroke-width="0.9"/>
          <line x1="4.4" y1="9" x2="13.6" y2="9" stroke="#fff" stroke-width="0.9"/>
        </svg>
        www.halvenmoor.com
      </li>
    </ul>
  </section>

  <section class="card card--brand" aria-label="Business card, brand side">
    <p class="brand">Halvenmoor</p>
  </section>

</body>
</html>
```